Looking for business card/letterhead/email signature

Take existing logo and create full design suite of collateral

Contact Information for Business Card

Use mock details that can be edited by us

Font styles to use
Sans Serif

```html
<!DOCTYPE html>
<html lang="en">
<head>
<meta charset="utf-8">
<title>Corvin Digital — Stationery Suite</title>
<link href="https://fonts.googleapis.com/css2?family=Montserrat:wght@400;700&family=Roboto:wght@400;500&display=swap" rel="stylesheet">
<style>
:root{
  --brand-blue:#0b4f93;
  --paper:#f7f7f7;
  --paper-white:#ffffff;
  --backdrop:#e3e3e3;
  --ink:#555a61;
  --ink-soft:#8a8e94;
  --on-blue:#ffffff;
}
*{box-sizing:border-box;margin:0;padding:0}
html,body{width:1200px;height:796px;overflow:hidden;background:var(--backdrop)}
body{position:relative;font-family:"Roboto",Arial,sans-serif;color:var(--ink)}
address{font-style:normal}
.sheet{position:absolute;background:var(--paper);overflow:hidden}
.band{position:absolute;right:0;background:var(--brand-blue);color:var(--on-blue)}
.wordmark{position:absolute;z-index:2;font-family:"Montserrat",Arial,sans-serif;font-weight:700;color:var(--brand-blue);white-space:nowrap;letter-spacing:-.02em;line-height:.95}
.wordmark span{display:block}
.wordmark.inline{display:flex;align-items:center;gap:.3em;line-height:1}
.wordmark .dot{width:.5em;height:.5em;border-radius:50%;background:currentColor}
.wordmark.on-blue{color:var(--on-blue)}
.contact{list-style:none;position:absolute;line-height:1.45}
.contact li{display:flex;align-items:center;gap:.4em}
.contact svg{width:.9em;height:.9em;fill:currentColor;flex:none}
.icons{position:absolute;width:0;height:0}

/* small business card back */
.card-back-sm{left:158px;top:357px;width:153px;height:88px;background:var(--brand-blue)}
.card-back-sm .wordmark{left:0;right:0;top:32px;justify-content:center;font-size:13px}
.card-back-sm .web{position:absolute;left:0;right:0;bottom:9px;text-align:center;font-size:3.6px;letter-spacing:.3em;color:var(--on-blue)}

/* small business card front */
.card-front-sm{left:158px;top:461px;width:154px;height:88px;background:var(--paper-white)}
.card-front-sm .band{left:46px;top:11px;height:32px}
.card-front-sm .wordmark{left:10px;top:18px;font-size:10px}
.card-front-sm .person{position:absolute;left:99px;top:21px;color:var(--on-blue)}
.card-front-sm .person strong{display:block;font-weight:500;font-size:6px}
.card-front-sm .person span{display:block;font-size:4px}
.card-front-sm .address{position:absolute;left:13px;top:65px;font-size:4px;line-height:1.3}
.card-front-sm .contact{left:100px;top:60px;font-size:3.8px}

/* letterhead */
.letterhead{left:342px;top:78px;width:336px;height:472px;background:var(--paper-white)}
.letterhead .band{left:99px;top:29px;height:45px;display:flex;align-items:center;gap:10px;padding-left:25px;font-size:4.3px}
.letterhead .band .col{line-height:1.5;padding-right:10px;border-right:.6px solid rgba(255,255,255,.8)}
.letterhead .band .col:last-child{border:0}
.letterhead .band .contact{position:static}
.letterhead .wordmark{left:26px;top:35px;font-size:18px}
.letter-body{position:absolute;left:30px;top:135px;width:276px;font-size:4.6px;line-height:1.55;color:var(--ink-soft)}
.letter-body .salutation{font-size:8px;color:var(--ink);margin-bottom:14px}
.letter-body p{margin-bottom:7px;text-align:justify}
.letter-body .closing{margin-top:14px}
.signature{display:block;width:64px;height:28px;margin-top:8px;background:linear-gradient(90deg,rgba(80,120,180,.25),rgba(80,120,180,.12));border-radius:3px}
.letterhead .web{position:absolute;left:0;right:0;top:454px;text-align:center;font-size:4.6px;letter-spacing:.35em;color:var(--ink-soft)}

/* presentation folder */
.folder{left:706px;top:50px;width:395px;height:501px;background:var(--brand-blue)}
.folder .spine{position:absolute;top:0;bottom:0;width:1px;background:rgba(255,255,255,.18)}
.folder .white-band{position:absolute;left:226px;right:0;top:198px;height:104px;background:var(--paper-white)}
.folder .wordmark{left:108px;top:220px;font-size:31px}

/* large business card */
.card-large{left:42px;top:606px;width:305px;height:148px;background:var(--paper-white)}
.card-large .band{left:94px;top:18px;height:54px}
.card-large .wordmark{left:22px;top:27px;font-size:19px}
.card-large .person{position:absolute;left:209px;top:33px;color:var(--on-blue)}
.card-large .person strong{display:block;font-weight:500;font-size:11px}
.card-large .person span{display:block;font-size:7px;margin-top:1px}
.card-large .address{position:absolute;left:22px;top:110px;font-size:6.6px;line-height:1.3}
.card-large .contact{left:210px;top:103px;font-size:6.6px;line-height:1.28}

/* envelope front */
.envelope-front{left:369px;top:580px;width:386px;height:176px;background:var(--paper-white)}
.envelope-front .band{left:103px;top:20px;height:48px}
.envelope-front .band .address{position:absolute;right:29px;top:19px;text-align:right;font-size:4.4px;line-height:1.35}
.envelope-front .wordmark{left:22px;top:26px;font-size:18px}

/* envelope back */
.envelope-back{left:774px;top:578px;width:386px;height:175px;background:var(--paper-white)}
.envelope-back .flap{position:absolute;left:0;right:0;top:0;height:54px;background:var(--brand-blue);border-radius:0 0 26px 26px}
.envelope-back .wordmark{left:0;right:0;top:22px;justify-content:center;font-size:12px}
</style>
</head>
<body>

<svg class="icons" aria-hidden="true">
  <defs>
    <symbol id="icon-phone" viewBox="0 0 16 16"><path d="M3.6 1.5l2.3 2.6-1.4 2a9 9 0 0 0 5.4 5.4l2-1.4 2.6 2.3-1.3 2.1C7.5 16 0 8.5 1.5 2.8z"/></symbol>
    <symbol id="icon-mobile" viewBox="0 0 16 16"><path d="M4 1h8v14H4zM5.5 2.5v9h5v-9zM7 12.8h2v1.2H7z" fill-rule="evenodd"/></symbol>
    <symbol id="icon-fax" viewBox="0 0 16 16"><path d="M4 1h8v4H4zM1 6h14v7h-3v2H4v-2H1zM5 10v4h6v-4z" fill-rule="evenodd"/></symbol>
    <symbol id="icon-mail" viewBox="0 0 16 16"><path d="M1 3h14v10H1zM2.5 4.5L8 9l5.5-4.5z" fill-rule="evenodd"/></symbol>
  </defs>
</svg>

<section class="sheet card-back-sm" aria-label="Business card, back">
  <div class="wordmark inline on-blue"><span class="dot"></span>Corvin Digital</div>
  <div class="web">www.corvindigital.example</div>
</section>

<section class="sheet card-front-sm" aria-label="Business card, front">
  <div class="band"></div>
  <div class="wordmark"><span>Corvin</span><span>Digital</span></div>
  <div class="person"><strong>ELLIS HALE</strong><span>CEO/FOUNDER</span></div>
  <address class="address">412 Cedar Row<br>Portland, Oregon 97201<br>www.corvindigital.example</address>
  <ul class="contact">
    <li><svg><use href="#icon-phone"/></svg>503 218 4470</li>
    <li><svg><use href="#icon-mobile"/></svg>503 662 1895</li>
    <li><svg><use href="#icon-fax"/></svg>503 218 4471</li>
    <li><svg><use href="#icon-mail"/></svg>hello@corvindigital.example</li>
  </ul>
</section>

<section class="sheet letterhead" aria-label="Letterhead">
  <div class="band">
    <address class="col">412 Cedar Row<br>Portland, Oregon 97201</address>
    <ul class="contact col">
      <li><svg><use href="#icon-phone"/></svg>503 218 4470</li>
      <li><svg><use href="#icon-mobile"/></svg>503 662 1895</li>
    </ul>
    <ul class="contact col">
      <li><svg><use href="#icon-fax"/></svg>503 218 4471</li>
      <li><svg><use href="#icon-mail"/></svg>hello@corvindigital.example</li>
    </ul>
  </div>
  <div class="wordmark"><span>Corvin</span><span>Digital</span></div>
  <div class="letter-body">
    <p class="salutation">Dear Mr. Hale,</p>
    <p>Thank you for meeting with our team last week. We enjoyed learning about your goals for the coming year and the ways your store reaches new customers online. This letter sums up what we discussed and the next steps we suggest.</p>
    <p>First, we will review your current website, search listings and social accounts to see where visitors arrive and where they leave. From that review we will draft a clear plan with timings, costs and the results you can expect.</p>
    <p>Second, our designers will refresh your pages so they load faster and read well on phones. Our writers will tidy product text and add short guides that answer the questions your customers ask most often. Each change will be tested before launch.</p>
    <p>Please let us know a good time to talk through this plan. We look forward to working with you.</p>
    <p class="closing">Sincerely,</p>
    <span class="signature" role="img" aria-label="Handwritten signature"></span>
  </div>
  <div class="web">www.corvindigital.example</div>
</section>

<section class="sheet folder" aria-label="Presentation folder">
  <span class="spine" style="left:11px"></span>
  <span class="spine" style="left:16px"></span>
  <span class="spine" style="left:22px"></span>
  <div class="white-band"></div>
  <div class="wordmark on-blue"><span>Corvin</span><span>Digital</span></div>
</section>

<section class="sheet card-large" aria-label="Business card, front, enlarged">
  <div class="band"></div>
  <div class="wordmark"><span>Corvin</span><span>Digital</span></div>
  <div class="person"><strong>ELLIS HALE</strong><span>CEO/FOUNDER</span></div>
  <address class="address">412 Cedar Row<br>Portland, Oregon 97201<br>www.corvindigital.example</address>
  <ul class="contact">
    <li><svg><use href="#icon-phone"/></svg>503 218 4470</li>
    <li><svg><use href="#icon-mobile"/></svg>503 662 1895</li>
    <li><svg><use href="#icon-fax"/></svg>503 218 4471</li>
    <li><svg><use href="#icon-mail"/></svg>hello@corvindigital.example</li>
  </ul>
</section>

<section class="sheet envelope-front" aria-label="Envelope, front">
  <div class="band"><address class="address">412 Cedar Row<br>Portland, Oregon 97201</address></div>
  <div class="wordmark"><span>Corvin</span><span>Digital</span></div>
</section>

<section class="sheet envelope-back" aria-label="Envelope, back">
  <div class="flap"></div>
  <div class="wordmark inline on-blue">Corvin Digital</div>
</section>

</body>
</html>
```